Tall ridge firewood

It a new firewood outlet in Jindabyne nsw that will only sell top hardwood firewood (ironbark , red gum, grey gum, an box mix. I would like to see a web page the we can do order online payment for delivery. It will all so need to have photos of the firewood. I all so have logo for tall ridge firewood
Must have a modem look but easy to use I would like to see a black back ground of some sort.

Here are some other firewood web pages for ideas and firewood info
http://www.example-logpile.com.au
http://www.example-stackwood.com.au
http://www.example-splitlog.com.au
http://www.example-kendaltimber.com.au/firewood

Industry/Entity Type

Firewood

```html
<!DOCTYPE html>
<html lang="en">
<head>
<meta charset="utf-8">
<title>Tall Ridge Firewood</title>
<link href="https://fonts.googleapis.com/css2?family=Oswald:wght@500;700&family=Open+Sans:wght@400;600;700&display=swap" rel="stylesheet">
<style>
:root{
  --bg-dark:#111;
  --blue:#1b6fbd;
  --blue-light:#2a86d6;
  --white:#fff;
  --text-light:#e6e6e6;
  --footer:#333;
  --line:#4a4a4a;
  --wood:#b98552;
  --wood-dark:#6e4a2a;
  --ink:#222;
}
*{margin:0;padding:0;box-sizing:border-box}
html,body{width:1093px;height:1200px;overflow:hidden}
body{position:relative;background:linear-gradient(90deg,#0c0c0c,#1b1b1b 30%,#0f0f0f 55%,#1d1d1d 80%,#0c0c0c);font-family:"Open Sans",sans-serif;color:var(--text-light);font-size:10.5px}
.abs{position:absolute}
a{color:inherit}
/* header */
.contact-line{left:146px;font-size:10px;color:var(--white);display:flex;align-items:center;gap:6px}
.contact-line.phone{top:20px}
.contact-line.mail{top:45px}
.phone-number{font-family:"Oswald",sans-serif;font-weight:700;font-size:17px}
.mail a{text-decoration:underline;color:#ddd}
.search{left:498px;top:28px;width:221px;height:26px;border:1px solid #777;border-radius:3px;background:#222;display:flex}
.search span{flex:1;padding:5px 8px;font-size:10px;color:#ccc}
.search-btn{width:25px;background:var(--blue);display:flex;align-items:center;justify-content:center;border-radius:0 2px 2px 0}
.cart{right:147px;top:20px;font-size:10px;color:var(--white);display:flex;align-items:center;gap:5px}
.cart b{font-family:"Oswald",sans-serif;font-size:12px}
.order-btn{left:851px;top:43px;width:95px;height:21px;background:linear-gradient(#fff,#ddd);border-radius:3px;color:var(--ink);font-size:10px;display:flex;align-items:center;justify-content:center}
/* nav */
.nav-band{left:0;top:92px;width:1093px;height:32px;background:var(--blue)}
.nav{left:146px;top:92px;height:32px;display:flex}
.nav a{text-decoration:none;color:var(--white);font-size:10px;display:flex;align-items:center;justify-content:center;border-right:1px solid #145a9b;height:32px}
.nav a.active{background:#2d2d2d}
/* hero */
.hero{left:146px;top:124px;width:800px;height:342px;background:var(--white)}
.brand{left:146px;top:124px;width:297px;height:342px;display:flex;flex-direction:column;align-items:center;justify-content:center;text-align:center}
.brand-name{display:flex;align-items:center;gap:8px;font-weight:700;font-size:19px;color:var(--blue)}
.brand-square{width:16px;height:16px;background:var(--blue)}
.brand-note{margin-top:8px;font-size:9px;color:#555}
.hero-photo{left:443px;top:132px;width:495px;height:326px;border:1px solid #555;background:radial-gradient(circle at 40% 40%,#c99b6a,var(--wood) 45%,var(--wood-dark))}
/* content */
h2{font-family:"Oswald",sans-serif;font-weight:700;color:var(--white);font-size:23px;letter-spacing:-0.3px}
.welcome-title{left:147px;top:492px}
.welcome-text{left:146px;top:537px;width:478px;line-height:12.6px}
.welcome-text p+p{margin-top:12px}
.divider{left:669px;top:498px;width:1px;height:192px;background:var(--line)}
.why-title{left:720px;top:492px}
.why-list{left:717px;top:536px;width:230px;list-style:none}
.why-list li{display:flex;gap:13px;margin-bottom:14px;line-height:12.6px}
.tick{flex:none;width:18px;height:18px;background:#4a4a4a;border-radius:3px;display:flex;align-items:center;justify-content:center;margin-top:2px}
.read-more{left:722px;top:668px;width:79px;height:21px;background:var(--blue);border-radius:3px;color:var(--white);font-size:10px;display:flex;align-items:center;justify-content:center}
/* products */
.products-title{left:147px;top:724px}
.view-all{left:902px;top:734px;font-size:10px;text-decoration:underline;color:var(--white)}
.products-rule{left:146px;top:767px;width:800px;height:1px;background:var(--line)}
.arrow{top:825px}
.product{top:795px;width:162px;text-align:center}
.product-photo{width:162px;height:115px;border:3px solid #ddd}
.product-name{margin-top:16px;font-size:14px;color:var(--white)}
.product-price{margin-top:6px;font-family:"Oswald",sans-serif;font-weight:700;font-size:14px;color:var(--blue-light)}
/* footer */
.footer{left:0;top:1005px;width:1093px;height:163px;background:var(--footer)}
.foot-col{top:1026px}
.foot-col h4{font-size:10px;font-weight:700;color:var(--white);margin-bottom:10px}
.foot-col ul{list-style:none;font-size:9.5px;color:var(--white);line-height:14.4px}
.foot-col li::before{content:"»";margin-right:6px}
.foot-sep{top:1028px;width:1px;height:117px;background:#555}
.social{display:flex;gap:5px}
.social span{width:24px;height:24px;display:block}
.happy h3{font-size:15px;font-weight:700;color:var(--white);margin-bottom:8px}
.happy p{font-size:10px;line-height:12.6px;color:#ddd;width:270px}
.happy .by{margin-top:12px}
.happy-btn{left:657px;top:1126px;width:80px;height:22px;background:linear-gradient(#fff,#ddd);border-radius:3px;color:var(--ink);font-size:10px;display:flex;align-items:center;justify-content:center}
.bottom-bar{left:0;top:1168px;width:1093px;height:32px;background:var(--blue);color:var(--white);font-size:10px;display:flex;align-items:center;justify-content:center}
</style>
</head>
<body>

<div class="abs contact-line phone">
  <svg width="12" height="14" viewBox="0 0 12 14"><path d="M3 1l2 3-1.5 1.5c.7 1.8 1.8 3 3.5 4L8.5 8l3 2-1 3C5 13 1 8 1 2z" fill="#aaa"/></svg>
  CALL US - <span class="phone-number">5550 318 742</span>
</div>
<div class="abs contact-line mail">
  <svg width="12" height="9" viewBox="0 0 12 9"><rect x=".5" y=".5" width="11" height="8" fill="none" stroke="#aaa"/><path d="M.5.5l5.5 4 5.5-4" fill="none" stroke="#aaa"/></svg>
  EMAIL US - <a href="#">INFO@TALLRIDGEFIREWOOD.EXAMPLE</a>
</div>

<div class="abs search">
  <span>Find Firewood Products ..</span>
  <div class="search-btn"><svg width="12" height="12" viewBox="0 0 12 12"><circle cx="5" cy="5" r="3.5" fill="none" stroke="#fff" stroke-width="2"/><path d="M7.5 7.5l3.5 3.5" stroke="#fff" stroke-width="2"/></svg></div>
</div>

<div class="abs cart">
  <svg width="13" height="11" viewBox="0 0 13 11"><path d="M0 1h2.5l2 6h6l1.5-4.5H4" fill="none" stroke="#ccc"/><circle cx="5" cy="9.5" r="1" fill="#ccc"/><circle cx="10" cy="9.5" r="1" fill="#ccc"/></svg>
  MY CART - <b>0 ITEM (S)</b>
</div>
<div class="abs order-btn">ORDER ONLINE</div>

<div class="abs nav-band"></div>
<nav class="abs nav">
  <a class="active" style="width:100px" href="#">HOME</a>
  <a style="width:112px" href="#">ABOUT US</a>
  <a style="width:117px" href="#">PRODUCTS</a>
  <a style="width:129px" href="#">ACCESSORIES</a>
  <a style="width:114px" href="#">DELIVERY</a>
  <a style="width:98px" href="#">FAQ`S</a>
  <a style="width:130px;border-right:0" href="#">CONTACT US</a>
</nav>

<div class="abs hero"></div>
<div class="abs brand">
  <div class="brand-name"><span class="brand-square"></span>TALL RIDGE FIREWOOD</div>
  <div class="brand-note">Hardwood firewood delivered in Jindabyne</div>
</div>
<div class="abs hero-photo" role="img" aria-label="Pile of cut hardwood firewood logs"></div>

<h2 class="abs welcome-title">Welcome to Tall Ridge Firewood</h2>
<div class="abs welcome-text">
  <p>Lorem ipsum dolor sit amet, consectetur adipisicing elit, sed do eiusmod tempor incididunt ut labore et dolore magna aliqua. Ut enim ad minim veniam, quis nostrud exercitation ullamco laboris nisi ut aliquip ex ea commodo consequat. Duis aute irure dolor in reprehenderit in voluptate velit esse cillum dolore eu fugiat nulla pariatur. Excepteur sint occaecat cupidatat non proident, sunt in culpa qui officia deserunt mollit anim id est laborum.</p>
  <p>Lorem ipsum dolor sit amet, consectetur adipisicing elit, sed do eiusmod tempor incididunt ut labore et dolore magna aliqua. Ut enim ad minim veniam, quis nostrud exercitation ullamco laboris nisi ut aliquip ex ea commodo consequat. Duis aute irure dolor in reprehenderit in voluptate velit esse cillum dolore eu fugiat nulla pariatur. Excepteur sint occaecat cupidatat non proident, sunt in culpa qui officia deserunt mollit anim id est laborum.</p>
</div>
<div class="abs divider"></div>

<h2 class="abs why-title">Why Choose Us ?</h2>
<ul class="abs why-list">
  <li><span class="tick"><svg width="10" height="8" viewBox="0 0 10 8"><path d="M1 4l3 3 5-6" fill="none" stroke="#ccc" stroke-width="2"/></svg></span>Lorem ipsum dolor sit amet, consectetur adipisicing elit.</li>
  <li><span class="tick"><svg width="10" height="8" viewBox="0 0 10 8"><path d="M1 4l3 3 5-6" fill="none" stroke="#ccc" stroke-width="2"/></svg></span>Lorem ipsum dolor sit amet, consectetur adipisicing elit, sed do eiusmod tempor.</li>
  <li><span class="tick"><svg width="10" height="8" viewBox="0 0 10 8"><path d="M1 4l3 3 5-6" fill="none" stroke="#ccc" stroke-width="2"/></svg></span>Lorem ipsum dolor sit amet, consectetur adipisicing elit, sed do.</li>
</ul>
<div class="abs read-more">READ MORE</div>

<h2 class="abs products-title">Top Hardwood Firewood Products</h2>
<a class="abs view-all" href="#">VIEW ALL</a>
<div class="abs products-rule"></div>

<svg class="abs arrow" style="left:146px" width="12" height="57" viewBox="0 0 12 57"><path d="M11 1L1 28.5 11 56" fill="none" stroke="#ddd"/></svg>
<svg class="abs arrow" style="left:935px" width="12" height="57" viewBox="0 0 12 57"><path d="M1 1l10 27.5L1 56" fill="none" stroke="#ddd"/></svg>

<div class="abs product" style="left:181px">
  <div class="product-photo" role="img" aria-label="Split ironbark firewood in a trailer" style="background:linear-gradient(#8a5a48,#a06b5a 55%,#555 75%,#777)"></div>
  <div class="product-name">Ironbark</div><div class="product-price">$30.20 Only</div>
</div>
<div class="abs product" style="left:371px">
  <div class="product-photo" role="img" aria-label="Split red gum firewood being handled" style="background:linear-gradient(120deg,#7a3322,#a84a36 50%,#5a2a1c)"></div>
  <div class="product-name">Red Gum</div><div class="product-price">$30.20 Only</div>
</div>
<div class="abs product" style="left:561px">
  <div class="product-photo" role="img" aria-label="Grey gum firewood logs" style="background:radial-gradient(circle,#9da2a8,#6f747a 60%,#4d5157)"></div>
  <div class="product-name">Grey Gum</div><div class="product-price">$30.20 Only</div>
</div>
<div class="abs product" style="left:750px">
  <div class="product-photo" role="img" aria-label="Box mix firewood burning in a fireplace" style="background:radial-gradient(ellipse at 50% 60%,#e0662a,#7a2a10 35%,#141414 65%)"></div>
  <div class="product-name">Box Mix</div><div class="product-price">$30.20 Only</div>
</div>

<footer class="abs footer"></footer>
<div class="abs foot-col" style="left:180px">
  <h4>NAVIGATION</h4>
  <ul><li>Home</li><li>About Us</li><li>Products</li><li>Accessories</li><li>Delivery</li><li>Faq`s</li><li>Contact Us</li></ul>
</div>
<div class="abs foot-sep" style="left:295px"></div>
<div class="abs foot-col" style="left:337px">
  <h4>PRODUCTS</h4>
  <ul><li>Ironbark</li><li>Red gum</li><li>Grey gum</li><li>Box mix</li></ul>
</div>
<div class="abs foot-sep" style="left:433px"></div>
<div class="abs foot-col" style="left:468px">
  <h4>FOLLOW US ON</h4>
  <div class="social"><span style="background:#3b5998"></span><span style="background:#1da1f2"></span><span style="background:#0e76a8"></span><span style="background:#dd4b39"></span></div>
</div>
<div class="abs foot-sep" style="left:619px"></div>
<div class="abs foot-col happy" style="left:656px;top:1022px">
  <h3>Happy Client`s</h3>
  <p>Lorem ipsum dolor sit amet, consectetur adipisicing elit, sed do eiusmod tempor incididunt ut labore et dolore magna aliqua.</p>
  <p class="by"><b style="color:#fff">Sam</b>. 15/06/13</p>
</div>
<div class="abs happy-btn">READ MORE</div>

<div class="abs bottom-bar">COPYRIGHT ©&nbsp;<b>TALL RIDGE FIREWOOD</b>&nbsp;2013. ALL RIGHT RESERVED.</div>

</body>
</html>
```